BRISK requires an exciting new business card

New business card required for BRISK. We are a new market research consultancy and want our brand to be approachable and be contemporary/modern, bold, uncomplicated/simple, and use friendly and easy to read fonts.

A draft website front page is attached to give you a feel (the pictures will be improved over the coming days).

The business card will be printed on 600gsm card, full colour both sides. The card is unique in that it allows one of four colours to be placed within the seam of the card (see http://uk.prentvo.com/products/gilt/business-cards.html)

The logo has been designed in yellow on white, white on yellow, yellow on black and black on yellow - please select whichever you feel most appropriate from the attached document (please use the versions with the tagline). I think my preference is yellow on white for the front, and then yellow or black as the dominant colour on the back.

Telephone numbers will be given next week as they are now being finalised.

Thanks

Target Market(s)

Professionals in large corporates, such as Marketing Managers at Grovane, Fizzaro Pop, Delmarco etc.

Industry/Entity Type

Market Research

Requirements
Must have
• Dana Pruitt FQRP
brisk
Level 4, 37 Quarrell St
Surrey Hills
NSW 2010
Tel: 02 XXXX XXXX
Mob: XXXX XXXXXX
Email: dana@briskqr.com.au
Web: www.briskqr.com.au

```html
<!DOCTYPE html>
<html lang="en">
<head>
<meta charset="utf-8">
<title>brisk — business card</title>
<link rel="stylesheet" href="https://fonts.googleapis.com/css2?family=Montserrat:wght@300;400;700&display=swap">
<style>
  :root {
    --brand-yellow: #e9c22b;
    --ink-dark: #3f3b3b;
    --ink-grey: #5a5858;
    --card-white: #ffffff;
    --backdrop: #ececec;
    --card-shadow: rgba(0, 0, 0, 0.14);
  }
  * { box-sizing: border-box; margin: 0; padding: 0; }
  html, body {
    width: 1200px;
    height: 1000px;
    overflow: hidden;
    background: var(--backdrop);
    font-family: "Montserrat", Arial, sans-serif;
  }
  .card-set {
    position: absolute;
    top: 347px;
    left: 70px;
    display: flex;
    gap: 60px;
  }
  .card {
    position: relative;
    width: 500px;
    height: 305px;
    box-shadow: 0 10px 28px var(--card-shadow);
    overflow: hidden;
  }

  /* Front */
  .card--front { background: var(--card-white); }
  .brand {
    position: absolute;
    font-weight: 700;
    letter-spacing: -1px;
    line-height: 1;
    white-space: nowrap;
  }
  .card--front .brand {
    top: 66px;
    left: 44px;
    font-size: 54px;
    color: var(--brand-yellow);
  }
  .tagline {
    position: absolute;
    font-weight: 300;
    color: var(--ink-grey);
    white-space: nowrap;
  }
  .card--front .tagline {
    top: 126px;
    left: 48px;
    font-size: 12px;
  }
  .holder {
    position: absolute;
    top: 176px;
    left: 84px;
    color: var(--ink-grey);
  }
  .holder__name { font-size: 20px; font-weight: 400; }
  .holder__title { font-size: 11px; font-weight: 400; margin-top: 2px; }

  .contact-list {
    position: absolute;
    top: 78px;
    left: 290px;
    list-style: none;
    font-size: 12px;
    font-weight: 400;
    color: var(--ink-grey);
  }
  .contact-list__item {
    display: flex;
    align-items: flex-start;
    gap: 12px;
    margin-bottom: 10px;
    line-height: 1.25;
    white-space: nowrap;
  }
  .contact-list__icon {
    flex: none;
    width: 18px;
    height: 18px;
    border-radius: 50%;
    background: var(--brand-yellow);
    display: flex;
    align-items: center;
    justify-content: center;
  }
  .contact-list__icon svg { width: 10px; height: 10px; fill: var(--card-white); }

  /* Back */
  .card--back { background: var(--brand-yellow); }
  .card--back .brand {
    top: 96px;
    left: 0;
    width: 100%;
    text-align: center;
    font-size: 92px;
    color: var(--ink-dark);
  }
  .card--back .tagline {
    top: 196px;
    left: 0;
    width: 100%;
    text-align: center;
    font-size: 17px;
    color: var(--ink-dark);
  }
  .web-address {
    position: absolute;
    bottom: 40px;
    width: 100%;
    text-align: center;
    font-size: 13px;
    letter-spacing: 3px;
    color: var(--ink-dark);
  }
</style>
</head>
<body>
  <main class="card-set">
    <section class="card card--front" aria-label="Business card front">
      <div class="brand">brisk</div>
      <p class="tagline">clear thinking research</p>
      <div class="holder">
        <p class="holder__name">Dana Pruitt</p>
        <p class="holder__title">FQRP</p>
      </div>
      <ul class="contact-list">
        <li class="contact-list__item">
          <span class="contact-list__icon"><svg viewBox="0 0 10 10"><path d="M2 0.5 L3.6 0.5 L4.2 2.8 L3.1 3.7 Q4 5.9 6.3 6.9 L7.2 5.8 L9.5 6.4 L9.5 8 Q9.5 9.5 8 9.5 Q0.5 8.5 0.5 2 Q0.5 0.5 2 0.5 Z"/></svg></span>
          <span>02 XXXX XXXX</span>
        </li>
        <li class="contact-list__item">
          <span class="contact-list__icon"><svg viewBox="0 0 10 10"><path d="M2.5 0 H7.5 V10 H2.5 Z M3.3 1.2 V7.8 H6.7 V1.2 Z" fill-rule="evenodd"/></svg></span>
          <span>XXXX XXXXXX</span>
        </li>
        <li class="contact-list__item">
          <span class="contact-list__icon"><svg viewBox="0 0 10 10"><path d="M0.5 2 H9.5 V8 H0.5 Z M1.2 2.6 L5 5.4 L8.8 2.6 Z" fill-rule="evenodd"/></svg></span>
          <span>dana@briskqr.com.au</span>
        </li>
        <li class="contact-list__item">
          <span class="contact-list__icon"><svg viewBox="0 0 10 10"><path d="M5 0.3 A3.4 3.4 0 0 1 8.4 3.7 Q8.4 6 5 9.8 Q1.6 6 1.6 3.7 A3.4 3.4 0 0 1 5 0.3 Z M5 2.4 A1.3 1.3 0 1 0 5 5 A1.3 1.3 0 1 0 5 2.4 Z" fill-rule="evenodd"/></svg></span>
          <span>Level 4, 37 Quarrell St<br>Hollowell Park, NSW 2041</span>
        </li>
      </ul>
    </section>

    <section class="card card--back" aria-label="Business card back">
      <div class="brand">brisk</div>
      <p class="tagline">clear thinking research</p>
      <p class="web-address">www.briskqr.com.au</p>
    </section>
  </main>
</body>
</html>
```